Modern looking signage for dental office.

Exterior signage for passing cars
Updates
Need extra days to review
Target Market(s)
Cars passing by
Font styles to use
Sans Serif
Colors
3276b5
Requirements
Must have
- Logo
- OPEN ON SUTURDAY AND SUNDAY
- NIGHT CLINIC AVAILABLE
- PLEASE USE THE FONT TYPE IN FILE 4 UPLOADED BELOW.
- (847) 302-7469
- Modern looking

```html
<!DOCTYPE html>
<html lang="en">
<head>
<meta charset="utf-8">
<title>Bright Arc Dental – Weekend &amp; Night Clinic Sign</title>
<link href="https://fonts.googleapis.com/css2?family=Josefin+Sans:wght@300&family=Open+Sans:wght@300;400;700;800&family=Roboto+Condensed:wght@400&display=swap" rel="stylesheet">
<style>
  :root {
    --teal: #27899f;
    --teal-dark: #1f7187;
    --ink: #111418;
    --logo-grey: #555559;
    --white: #ffffff;
    --silver-light: #f2f2f2;
    --silver-mid: #b9b9b9;
  }
  * { margin: 0; padding: 0; box-sizing: border-box; }
  html, body { width: 1200px; height: 1200px; overflow: hidden; background: var(--white); }
  .sign {
    position: relative;
    width: 1200px;
    height: 1200px;
    overflow: hidden;
    font-family: "Open Sans", sans-serif;
  }
  .clinic-backdrop {
    position: absolute;
    inset: 0;
    background:
      radial-gradient(ellipse 420px 600px at 930px 520px, rgba(255,255,255,0.95), rgba(255,255,255,0) 70%),
      linear-gradient(120deg, #e9ecea 0%, #f6f7f6 35%, #eef3f2 60%, #f3f4f6 100%);
  }
  .base-curve { position: absolute; inset: 0; width: 1200px; height: 1200px; }
  .brand {
    position: absolute;
    left: 120px;
    top: 78px;
    display: flex;
    align-items: center;
    gap: 34px;
  }
  .brand-circle {
    width: 204px;
    height: 204px;
    border: 3px solid var(--logo-grey);
    border-radius: 50%;
  }
  .brand-name {
    font-family: "Josefin Sans", sans-serif;
    font-weight: 300;
    font-size: 76px;
    color: var(--logo-grey);
    letter-spacing: 1px;
    white-space: nowrap;
    line-height: 1;
  }
  .tagline {
    position: absolute;
    left: 418px;
    top: 248px;
    font-family: "Roboto Condensed", sans-serif;
    font-size: 42px;
    color: var(--logo-grey);
    letter-spacing: 0.5px;
    white-space: nowrap;
  }
  .hours-panel {
    position: absolute;
    left: 107px;
    top: 340px;
    width: 978px;
    height: 322px;
    border-radius: 38px;
    background: linear-gradient(90deg, var(--teal) 0%, var(--teal) 60%, var(--teal-dark) 100%);
    opacity: 0.97;
    color: var(--white);
    text-align: center;
  }
  .hours-headline {
    font-weight: 800;
    font-size: 186px;
    line-height: 1;
    margin-top: 38px;
    letter-spacing: 2px;
    white-space: nowrap;
  }
  .hours-days {
    font-size: 71px;
    line-height: 1;
    margin-top: 6px;
    white-space: nowrap;
  }
  .hours-days strong { font-weight: 800; }
  .hours-days .joiner { font-weight: 300; }
  .night-clinic {
    position: absolute;
    left: 0;
    width: 1200px;
    top: 690px;
    text-align: center;
    font-size: 56px;
    color: var(--ink);
    white-space: nowrap;
  }
  .night-clinic strong { color: var(--teal); font-weight: 800; }
  .phone {
    position: absolute;
    left: 0;
    width: 1200px;
    top: 968px;
    text-align: center;
    font-weight: 800;
    font-size: 134px;
    line-height: 1;
    color: var(--white);
    letter-spacing: 1px;
  }
  .web {
    position: absolute;
    left: 0;
    width: 1200px;
    top: 1110px;
    text-align: center;
    font-size: 32px;
    color: var(--white);
    letter-spacing: 12px;
    white-space: nowrap;
  }
  .web .domain-name { font-weight: 700; }
  .web .domain-part { font-weight: 300; }
</style>
</head>
<body>
  <main class="sign">
    <div class="clinic-backdrop" role="img" aria-label="Soft blurred dental clinic interior with a large white tooth and a dental mirror"></div>

    <svg class="base-curve" viewBox="0 0 1200 1200" aria-hidden="true">
      <defs>
        <linearGradient id="silverBand" x1="0" y1="0" x2="1" y2="0">
          <stop offset="0" stop-color="#a8a8a8"/>
          <stop offset="0.35" stop-color="#e6e6e6"/>
          <stop offset="0.55" stop-color="#ffffff"/>
          <stop offset="0.8" stop-color="#cfcfcf"/>
          <stop offset="1" stop-color="#9e9e9e"/>
        </linearGradient>
      </defs>
      <path d="M0,720 Q600,1034 1200,720 L1200,1200 L0,1200 Z" fill="url(#silverBand)"/>
      <path d="M0,725 Q600,1190 1200,725 L1200,1200 L0,1200 Z" fill="var(--teal)"/>
      <path d="M0,725 Q600,1190 1200,725" fill="none" stroke="#ffffff" stroke-width="3"/>
    </svg>

    <header class="brand">
      <div class="brand-circle"></div>
      <div class="brand-name">BRIGHT ARC DENTAL</div>
    </header>
    <p class="tagline">MODERN GENERAL DENTISTRY</p>

    <section class="hours-panel">
      <h1 class="hours-headline">OPEN ON</h1>
      <p class="hours-days"><strong>SATURDAY</strong> <span class="joiner">AND</span> <strong>SUNDAY</strong></p>
    </section>

    <p class="night-clinic">Night clinic from <strong>5pm</strong> to <strong>10pm</strong></p>

    <p class="phone">847 302 7469</p>
    <p class="web"><span class="domain-part">www.</span><span class="domain-name">BrightArcDentalHill</span><span class="domain-part">.com</span></p>
  </main>
</body>
</html>
```